Flyer to advertise gutter cleaning throughout the Autumn and winter monthss

I need a new flyer to advertise gutter and driveway cleaning, roof and gutter repairs.

I am an experienced licensed Plumber and Gasfitter looking to broaden my scope of work to gutter cleaning. I am experienced in cleaning gutter and live in a area with large gum trees. I wont something that's clear, eye catching but not too busy.

Flyer requirements: Free roof inspection - no obligation. Gutter Cleaning from $199. Pictures of men using blower or hands to clean roof gutters (no obvious faces) to be included. Australian looking houses.

A mention that 'All general plumbing maintenance' is offered as other services but not too much wording about this as the target is for gutter cleaning.

Phone number: 0427 385 912 (in this format)
Business Name: Larkvale Plumbing & Gasfitting
License: 3175420
ABN: 71364058227
Web: http://larkvaleplumbing.example.site/

Target Market(s)

Elderly - busy working class

Industry/Entity Type

Plumber

Font styles to use
Sans Serif

Colors
0355a3
fbed22
ec1f27
f78f20

Requirements
Must have
• Roof Gutter Cleaning pictures
• Men in protective clothing if possible
Nice to have
• More information:
• Prevent against flooding, mold, rust, rotting and corrosion now!
• Gutter Cleaning Services
• • Remove leaves, sticks, and other debris
• • Clear away clogs
• • Test your downpipes
• • Pinpoint any gutter issues
• • Repair gutter
• With regular service, you can count on your property to be well-protected no matter what the forecast!
Should not have
• Houses that don't look Australian

```html
<!DOCTYPE html>
<html lang="en">
<head>
<meta charset="utf-8">
<title>Larkvale Plumbing &amp; Gasfitting – Gutter Cleaning Flyer</title>
<link href="https://fonts.googleapis.com/css2?family=Oswald:wght@500;700&family=Cabin:wght@400;600;700&display=swap" rel="stylesheet">
<style>
  :root{
    --blue:#0355a3;
    --blue-light:#1f74d4;
    --yellow:#fbed22;
    --red:#ec1f27;
    --dark:#231f20;
    --grey-text:#4a4a4a;
    --panel-grey:#cfcfcf;
    --page:#e9ecee;
  }
  *{box-sizing:border-box;margin:0;padding:0}
  html,body{width:1200px;height:1200px;overflow:hidden;background:var(--page)}
  .flyer{
    position:absolute;left:189px;top:6px;width:842px;height:1188px;
    transform:scale(0.9764);transform-origin:0 0;
    background:#fff;overflow:hidden;font-family:"Cabin",sans-serif;
    box-shadow:0 4px 18px rgba(0,0,0,.18);
  }
  .hero-photo{
    position:absolute;left:0;top:0;width:842px;height:470px;
    background:linear-gradient(110deg,#6f8f4e 0%,#8fae6a 30%,#5a5a52 55%,#6d6a66 75%,#4f4c49 100%);
  }
  .hero-curves{position:absolute;left:0;top:0}
  .badge{
    position:absolute;left:600px;top:285px;width:212px;height:212px;border-radius:50%;
    background:#fff;border:6px solid var(--yellow);box-shadow:0 3px 8px rgba(0,0,0,.25);
    text-align:center;font-family:"Oswald",sans-serif;font-weight:700;padding-top:42px;
  }
  .badge-free{color:var(--red);font-size:70px;line-height:66px;letter-spacing:1px}
  .badge-line1{color:var(--blue);font-size:20px;line-height:26px;margin-top:4px}
  .badge-line2{color:var(--dark);font-size:22px;line-height:26px}
  .brand{position:absolute;left:38px;top:508px;display:flex;align-items:center;gap:14px}
  .brand-dot{width:56px;height:56px;border-radius:50%;background:var(--blue)}
  .brand-name{font-size:22px;font-weight:600;color:var(--dark);line-height:25px}
  .headline{position:absolute;left:36px;top:612px;width:330px;font-family:"Oswald",sans-serif;font-weight:700;text-transform:uppercase}
  .headline span{display:block;white-space:nowrap}
  .hl-grey{color:var(--grey-text)}
  .hl-blue{color:var(--blue)}
  .hl-1{font-size:40px;line-height:50px}
  .hl-2{font-size:80px;line-height:86px;letter-spacing:1px}
  .hl-3{font-size:52px;line-height:60px}
  .hl-4{font-size:92px;line-height:94px;letter-spacing:1px}
  .tagline{position:absolute;left:38px;top:910px;width:326px;font-size:16px;line-height:21px;color:var(--dark);text-align:justify}
  .call{
    position:absolute;left:92px;top:980px;width:206px;height:72px;border:2px solid #cfcfcf;border-radius:10px;
    text-align:center;box-shadow:0 4px 6px rgba(0,0,0,.12);padding-top:6px;
  }
  .call-label{font-size:25px;color:var(--dark);line-height:30px}
  .call-number{font-size:22px;color:var(--red);line-height:28px;display:flex;justify-content:center;align-items:center;gap:8px}
  .info-panel{
    position:absolute;left:432px;top:470px;width:372px;height:420px;border-radius:0 0 12px 12px;
    background:linear-gradient(180deg,var(--blue-light) 0%,var(--blue) 100%);color:#fff;padding:52px 28px 0 28px;
  }
  .info-lead{font-size:19px;font-weight:700;line-height:24px}
  .info-title{font-size:17px;font-weight:700;color:var(--yellow);margin-top:20px}
  .service-list{list-style:none;margin-top:6px}
  .service-list li{font-size:16px;line-height:31px;display:flex;align-items:center;gap:12px;padding-left:4px}
  .info-close{font-size:19px;line-height:24px;margin-top:16px;text-align:justify}
  .price{
    position:absolute;left:445px;top:915px;width:345px;height:137px;background:var(--panel-grey);
    box-shadow:0 6px 8px rgba(0,0,0,.18);padding:10px;
  }
  .price-inner{height:100%;border:2px dashed #a9a9a9;text-align:center;padding-top:14px}
  .price-label{font-size:25px;color:var(--grey-text);line-height:30px}
  .price-amount{font-family:"Oswald",sans-serif;font-weight:700;font-size:52px;line-height:56px;color:var(--grey-text)}
  .price-amount em{font-style:normal;color:var(--red)}
  .footer-curves{position:absolute;left:0;top:1060px}
  .footer-text{position:absolute;left:0;top:1108px;width:842px;color:#fff;text-align:center}
  .footer-name{font-size:20px;font-weight:600;line-height:26px}
  .footer-details{display:flex;justify-content:center;gap:48px;font-size:16px;margin-top:9px}
  .footer-details b{font-weight:700}
</style>
</head>
<body>
<div class="flyer">
  <div class="hero-photo" role="img" aria-label="Photo of a gloved hand pulling leaves and debris from a roof gutter beside tiled roofing and gum trees"></div>
  <svg class="hero-curves" width="842" height="480" viewBox="0 0 842 480">
    <path d="M0,392 C200,448 480,458 842,292 L842,326 C480,472 200,470 0,418 Z" fill="#0355a3"/>
    <path d="M300,466 C560,458 720,400 842,318 L842,336 C720,418 560,470 300,470 Z" fill="#ec1f27"/>
    <path d="M0,418 C200,470 480,472 842,330 L842,480 L0,480 Z" fill="#fff"/>
  </svg>

  <div class="info-panel">
    <p class="info-lead">Prevent against flooding, mold, rust, rotting and corrosion now!</p>
    <p class="info-title">Gutter Cleaning Services</p>
    <ul class="service-list">
      <li><svg width="14" height="14" viewBox="0 0 14 14"><rect x="1" y="2" width="11" height="11" fill="none" stroke="#fbed22" stroke-width="1.4"/><path d="M3.5,7 L6,9.5 L12.5,2.5" fill="none" stroke="#fbed22" stroke-width="1.6"/></svg>Remove leaves, sticks, and other debris</li>
      <li><svg width="14" height="14" viewBox="0 0 14 14"><rect x="1" y="2" width="11" height="11" fill="none" stroke="#fbed22" stroke-width="1.4"/><path d="M3.5,7 L6,9.5 L12.5,2.5" fill="none" stroke="#fbed22" stroke-width="1.6"/></svg>Clear away clogs</li>
      <li><svg width="14" height="14" viewBox="0 0 14 14"><rect x="1" y="2" width="11" height="11" fill="none" stroke="#fbed22" stroke-width="1.4"/><path d="M3.5,7 L6,9.5 L12.5,2.5" fill="none" stroke="#fbed22" stroke-width="1.6"/></svg>Test your downpipes</li>
      <li><svg width="14" height="14" viewBox="0 0 14 14"><rect x="1" y="2" width="11" height="11" fill="none" stroke="#fbed22" stroke-width="1.4"/><path d="M3.5,7 L6,9.5 L12.5,2.5" fill="none" stroke="#fbed22" stroke-width="1.6"/></svg>Pinpoint any gutter issues</li>
      <li><svg width="14" height="14" viewBox="0 0 14 14"><rect x="1" y="2" width="11" height="11" fill="none" stroke="#fbed22" stroke-width="1.4"/><path d="M3.5,7 L6,9.5 L12.5,2.5" fill="none" stroke="#fbed22" stroke-width="1.6"/></svg>Repair gutter</li>
    </ul>
    <p class="info-close">With regular service, you can count on your property to be well-protected no matter what the forecast!</p>
  </div>

  <div class="badge">
    <div class="badge-free">FREE</div>
    <div class="badge-line1">ROOF INSPECTION</div>
    <div class="badge-line2">NO OBLIGATION</div>
  </div>

  <div class="brand">
    <div class="brand-dot"></div>
    <div class="brand-name">Larkvale Plumbing<br>&amp; Gasfitting</div>
  </div>

  <h1 class="headline">
    <span class="hl-grey hl-1">Gutter &amp; Driveway</span>
    <span class="hl-blue hl-2">Cleaning</span>
    <span class="hl-grey hl-3">Roof &amp; Gutter</span>
    <span class="hl-blue hl-4">Repairs</span>
  </h1>

  <p class="tagline">We offer a profession service for all your plumbing needs.</p>

  <div class="call">
    <div class="call-label">CALL US NOW</div>
    <div class="call-number">
      <svg width="20" height="20" viewBox="0 0 20 20"><circle cx="10" cy="10" r="9" fill="#0355a3"/><path d="M6.5,5.5 L8.5,5 L9.5,7.5 L8.3,8.5 C9,10 10,11 11.5,11.7 L12.5,10.5 L15,11.5 L14.5,13.5 C10,14 6,10 6.5,5.5 Z" fill="#fff"/></svg>
      0427 385 912
    </div>
  </div>

  <div class="price">
    <div class="price-inner">
      <div class="price-label">GUTTER CLEANING</div>
      <div class="price-amount">FROM <em>$199</em></div>
    </div>
  </div>

  <svg class="footer-curves" width="842" height="128" viewBox="0 0 842 128">
    <path d="M0,58 C250,20 560,14 842,62 L842,128 L0,128 Z" fill="#0355a3"/>
    <path d="M200,28 C450,10 680,18 842,50 L842,64 C680,30 450,22 200,28 Z" fill="#ec1f27"/>
    <path d="M0,66 C250,30 560,26 842,70 L842,128 L0,128 Z" fill="#fff"/>
    <path d="M0,74 C250,40 560,36 842,78 L842,128 L0,128 Z" fill="#231f20"/>
  </svg>
  <div class="footer-text">
    <div class="footer-name">LARKVALE PLUMBING &amp; GASFITTING</div>
    <div class="footer-details">
      <span><b>License:</b> 3175420</span>
      <span><b>ABN:</b> 71364058227</span>
      <span><b>Web:</b> http://larkvaleplumbing.example.site/</span>
    </div>
  </div>
</div>
</body>
</html>
```